New Year's card HTML

can you produce a best new years wishes 2018 design in HTML for our website as what I would like to send by email towards my network of candidates / customers ...

It must be wow, inspiring , design, meaningfull... MMM those people care about me, or those people will help me to go the extra mile, to help me to achieve my career goals, Your best move, enhance my possibilities, bring the love back

Target Market(s)

CEo's / CMO's/ HRDirectors network of 450k

Coding

Coded - Design and coding required

Number of Pages Required

1 page

Colors

Designer to choose colors to be used in the design.

Requirements
Must have
• Logo / visual / website adress www.moravintel.com and a call to action
Should not have
• no sound as our business is confidential

```html
<!DOCTYPE html>
<html lang="en">
<head>
<meta charset="utf-8">
<title>Moravintel – Happy New Year 2018</title>
<link rel="stylesheet" href="https://fonts.googleapis.com/css2?family=Cinzel:wght@400&family=Tinos:wght@700&family=Mulish:wght@400&display=swap">
<style>
  :root {
    --navy-deep: #07143a;
    --navy: #0c2356;
    --blue-mid: #0f4a8c;
    --cyan: #1cc3f0;
    --cyan-light: #8ae6ff;
    --band: #17b0e6;
    --white: #ffffff;
  }
  * { margin: 0; padding: 0; box-sizing: border-box; }
  html, body { width: 929px; height: 1200px; overflow: hidden; background: var(--navy-deep); }
  .card {
    position: relative;
    width: 929px;
    height: 1200px;
    overflow: hidden;
    background: var(--navy-deep);
  }
  .network-backdrop {
    position: absolute;
    inset: 0;
    background:
      radial-gradient(ellipse 420px 520px at 820px 880px, rgba(28,195,240,0.75), rgba(28,195,240,0) 70%),
      radial-gradient(ellipse 360px 300px at 470px 40px, rgba(40,150,230,0.55), rgba(40,150,230,0) 70%),
      radial-gradient(ellipse 300px 260px at 860px 560px, rgba(60,200,250,0.45), rgba(60,200,250,0) 70%),
      linear-gradient(180deg, var(--navy) 0%, var(--navy-deep) 45%, #0a2150 100%);
  }
  .brand {
    position: absolute;
    left: 0;
    top: 140px;
    width: 929px;
    display: flex;
    align-items: center;
    justify-content: center;
    gap: 34px;
  }
  .brand-mark {
    width: 54px;
    height: 54px;
    border-radius: 50%;
    background: var(--white);
  }
  .brand-name {
    font-family: "Cinzel", serif;
    font-weight: 400;
    font-size: 54px;
    letter-spacing: 3px;
    color: var(--white);
    line-height: 1;
  }
  .greeting-band {
    position: absolute;
    left: 0;
    top: 277px;
    width: 929px;
    height: 165px;
    background: linear-gradient(90deg, rgba(23,176,230,0.92) 0%, var(--band) 60%, rgba(23,176,230,0.55) 92%, rgba(23,176,230,0) 100%);
  }
  .greeting-band::before,
  .greeting-band::after {
    content: "";
    position: absolute;
    left: 90px;
    right: 40px;
    height: 16px;
    border-top: 2px solid rgba(200,245,255,0.75);
    border-bottom: 2px solid rgba(200,245,255,0.75);
  }
  .greeting-band::before { top: 12px; }
  .greeting-band::after { bottom: 12px; }
  .greeting {
    position: absolute;
    left: 0;
    width: 100%;
    top: 40px;
    text-align: center;
    font-family: "Cinzel", serif;
    font-weight: 400;
    font-size: 80px;
    letter-spacing: 2px;
    color: var(--white);
    line-height: 1;
    padding-left: 30px;
  }
  .year {
    position: absolute;
    left: 0;
    width: 929px;
    top: 470px;
    text-align: center;
    font-family: "Tinos", serif;
    font-weight: 700;
    font-size: 290px;
    line-height: 1;
    color: var(--white);
    letter-spacing: 4px;
    text-shadow: 0 6px 18px rgba(0,0,0,0.45);
  }
  .year-reflection {
    position: absolute;
    left: 0;
    width: 929px;
    top: 700px;
    text-align: center;
    font-family: "Tinos", serif;
    font-weight: 700;
    font-size: 290px;
    line-height: 1;
    letter-spacing: 4px;
    color: var(--white);
    transform: scaleY(-1);
    transform-origin: top;
    opacity: 0.35;
    -webkit-mask-image: linear-gradient(0deg, rgba(0,0,0,0) 72%, rgba(0,0,0,1) 100%);
    mask-image: linear-gradient(0deg, rgba(0,0,0,0) 72%, rgba(0,0,0,1) 100%);
    height: 290px;
    overflow: hidden;
    pointer-events: none;
  }
  .cta {
    position: absolute;
    left: 185px;
    top: 837px;
    width: 561px;
    height: 115px;
    border: 4px solid var(--white);
    border-radius: 58px;
    display: flex;
    align-items: center;
    justify-content: center;
    font-family: "Mulish", sans-serif;
    font-weight: 400;
    font-size: 36px;
    letter-spacing: 0.5px;
    color: var(--white);
    text-decoration: none;
  }
</style>
</head>
<body>
  <main class="card">
    <div class="network-backdrop" role="img" aria-label="Glowing blue network of connected points and translucent triangles with small hexagons on a deep navy background"></div>

    <header class="brand">
      <span class="brand-mark"></span>
      <span class="brand-name">MORAVINTEL</span>
    </header>

    <div class="greeting-band">
      <h1 class="greeting">HAPPY NEW YEAR</h1>
    </div>

    <p class="year">2018</p>
    <p class="year-reflection" aria-hidden="true">2018</p>

    <a class="cta" href="https://www.moravintel.com">VISIT OUR WEBSITE</a>
  </main>
</body>
</html>
```